product development company BRVEMKO LLC business card

We need a business card design for a company based in Texas called 'BRVEMKO LLC'. Our first product is a illuminated portable ice chest that is called ' Copper Harbor coolers'. Copper harbor coolers is trademarked. I would like to have the copper harbor trademark somewhere on the card as well as the BRVEMKO LLC name.

Target Market(s)

outdoor industry

Industry/Entity Type

Business

Contact Information for Business Card

i would like to have BRVEMKO LLC logo larger than the Copper harbor coolers logo.

Font styles to use
Serif
Sans Serif

```html
<!DOCTYPE html>
<html lang="en">
<head>
<meta charset="utf-8">
<title>BRVEMKO LLC Business Card</title>
<link href="https://fonts.googleapis.com/css2?family=Open+Sans:wght@400;700&display=swap" rel="stylesheet">
<style>
  :root {
    --backdrop: #6e4b35;
    --card-front: #a6a6a6;
    --card-back: #161616;
    --ink-dark: #1c1c1c;
    --ink-light: #f4f4f4;
  }
  * { margin: 0; padding: 0; box-sizing: border-box; }
  html, body { width: 1200px; height: 1000px; overflow: hidden; }
  body {
    background: var(--backdrop);
    font-family: "Open Sans", Arial, sans-serif;
    position: relative;
  }
  .card {
    position: absolute;
    left: 265px;
    width: 665px;
    height: 397px;
    box-shadow: 0 4px 10px rgba(0,0,0,0.45);
  }
  .card-front { top: 73px; background: var(--card-front); color: var(--ink-dark); }
  .card-back { top: 532px; background: var(--card-back); color: var(--ink-light); }

  .company-name {
    position: absolute;
    left: 34px;
    top: 44px;
    font-size: 38px;
    font-weight: 700;
    letter-spacing: 1px;
    line-height: 1;
  }
  .person { position: absolute; left: 33px; top: 183px; }
  .person-name { font-size: 20px; font-weight: 700; line-height: 1.2; }
  .person-title { font-size: 15px; line-height: 1.3; }

  .contact-list {
    position: absolute;
    left: 33px;
    top: 245px;
    list-style: none;
    font-size: 15px;
  }
  .contact-list li {
    display: flex;
    align-items: center;
    height: 23px;
  }
  .contact-list .address { margin-top: 4px; }
  .contact-list svg { width: 16px; height: 16px; margin-right: 7px; fill: var(--ink-dark); }

  .product-name {
    position: absolute;
    left: 418px;
    top: 274px;
    display: flex;
    align-items: center;
    font-size: 18px;
    font-weight: 700;
  }
  .product-name .mark-square {
    width: 26px; height: 26px;
    background: var(--ink-dark);
    margin-right: 10px;
  }

  .company-name-back {
    position: absolute;
    left: 0; right: 0;
    top: 160px;
    text-align: center;
    font-size: 46px;
    font-weight: 700;
    letter-spacing: 2px;
    line-height: 1;
  }
</style>
</head>
<body>
  <section class="card card-front">
    <div class="company-name">BRVEMKO LLC</div>

    <div class="person">
      <div class="person-name">MARCUS ELLERY</div>
      <div class="person-title">Managing Director</div>
    </div>

    <ul class="contact-list">
      <li>
        <svg viewBox="0 0 16 16" aria-hidden="true"><path d="M5 1h6a1 1 0 0 1 1 1v12a1 1 0 0 1-1 1H5a1 1 0 0 1-1-1V2a1 1 0 0 1 1-1zm0 2v8h6V3zm3 9.2a.9.9 0 1 0 0 1.8.9.9 0 0 0 0-1.8z"/></svg>
        + 000 000 0000
      </li>
      <li>
        <svg viewBox="0 0 16 16" aria-hidden="true"><path d="M1 6c0-2 3-3 7-3s7 1 7 3v1h-4V5.5H5V7H1zm3 2h8l2 6H2zm4 1.5a1.8 1.8 0 1 0 0 3.6 1.8 1.8 0 0 0 0-3.6z"/></svg>
        + 000 000 0000
      </li>
      <li>
        <svg viewBox="0 0 16 16" aria-hidden="true"><path d="M1 4h14v9H1zm1.2 1 5.8 4.3L13.8 5z"/></svg>
        info@brvemkocopperharbor.com
      </li>
      <li>
        <svg viewBox="0 0 16 16" aria-hidden="true"><path d="M8 1a7 7 0 1 0 0 14A7 7 0 0 0 8 1zm0 1.5c.8 0 1.7 1.6 2 4H6c.3-2.4 1.2-4 2-4zM2.6 7.5h2.3c0 .4 0 .7.1 1H2.6zm8.4 0h2.4v1H11zM6 9.5h4c-.3 2.4-1.2 4-2 4s-1.7-1.6-2-4z"/></svg>
        www.brvemkocopperharbor.com
      </li>
      <li class="address">
        <svg viewBox="0 0 16 16" aria-hidden="true"><path d="M8 0a5.5 5.5 0 0 0-5.5 5.5C2.5 10 8 16 8 16s5.5-6 5.5-10.5A5.5 5.5 0 0 0 8 0zm0 3.5a2 2 0 1 1 0 4 2 2 0 0 1 0-4z"/></svg>
        1418 W. Alder Ave. Sealy, TX 77474
      </li>
    </ul>

    <div class="product-name">
      <span class="mark-square"></span>
      Copper Harbor Coolers
    </div>
  </section>

  <section class="card card-back">
    <div class="company-name-back">BRVEMKO LLC</div>
  </section>
</body>
</html>
```